Banner Ad for Weight Loss Product Site

We need a banner ad design for a new company selling a weight loss online programme (Ebook). The product is called "Your FitRoute" and is suitable for people that want to lose weight fast and without doing sports, regardless of age. We would like to see designs that are eye-catching and at its best animated like in the example files. The final design should exhibit a professional look that encourages the customers to buy our product. The text should be "Persönlicher Diätplan zum Abnehmen?" as a title and "Jetzt informieren" for the button field. Thank you!

Industry/Entity Type

Weight

```html
<!DOCTYPE html>
<html lang="de">
<head>
<meta charset="utf-8">
<title>Your FitRoute – Banner</title>
<link href="https://fonts.googleapis.com/css2?family=Open+Sans:wght@700;800&family=Roboto+Condensed:wght@700&display=swap" rel="stylesheet">
<style>
  :root {
    --page-bg: #efefef;
    --banner-white: #ffffff;
    --green-dark: #3f9a1f;
    --green-main: #62b72a;
    --green-light: #9ed24a;
    --swoosh-yellow: #e9f08a;
    --title-green: #3aa52a;
    --button-top: #ffcf3a;
    --button-bottom: #f39a0c;
    --button-text: #4a2a06;
    --button-chip: #3b2a16;
    --logo-circle: #2f7d16;
    --caption-grey: #6d6d6d;
    --photo-skin-a: #e9b99a;
    --photo-skin-b: #c98a66;
    --product-a: #f4f4f4;
    --product-b: #cfe3b8;
  }
  * { margin: 0; padding: 0; box-sizing: border-box; }
  html, body { width: 1200px; height: 721px; overflow: hidden; }
  body {
    background: var(--page-bg);
    position: relative;
    font-family: "Open Sans", Arial, sans-serif;
  }
  .banner {
    position: absolute;
    left: 296px; top: 0;
    width: 548px; height: 544px;
    background: var(--banner-white);
    overflow: hidden;
  }
  .banner__bands { position: absolute; inset: 0; }
  .banner__title {
    position: absolute;
    left: 26px; top: 86px;
    width: 340px;
    color: var(--title-green);
    font-weight: 800;
    font-size: 44px;
    line-height: 1.12;
    letter-spacing: -0.3px;
  }
  .banner__cursor { position: absolute; left: 48px; top: 266px; }
  .banner__photo {
    position: absolute;
    right: 0; top: 0;
    width: 200px; height: 470px;
    background: linear-gradient(180deg, #7a4a34 0%, var(--photo-skin-a) 30%, var(--photo-skin-b) 65%, #2a2a2a 100%);
    border-radius: 90px 0 0 0;
  }
  .banner__product {
    position: absolute;
    left: 150px; top: 282px;
    width: 164px; height: 162px;
    background: linear-gradient(135deg, var(--product-a) 0%, var(--product-b) 100%);
    border-radius: 6px;
  }
  .brand {
    position: absolute;
    left: 6px; top: 370px;
    width: 166px; height: 166px;
    border-radius: 50%;
    background: var(--logo-circle);
    display: flex; align-items: center; justify-content: center;
    text-align: center;
  }
  .brand__name {
    color: #ffffff;
    font-weight: 800;
    font-size: 26px;
    line-height: 1.05;
  }
  .cta {
    position: absolute;
    left: 222px; top: 468px;
    width: 306px; height: 54px;
    border-radius: 27px;
    background: linear-gradient(180deg, var(--button-top) 0%, var(--button-bottom) 100%);
    display: flex; align-items: center; justify-content: center;
    gap: 16px;
    box-shadow: 0 2px 3px rgba(0,0,0,.25);
  }
  .cta__label {
    font-family: "Roboto Condensed", Arial, sans-serif;
    font-weight: 700;
    font-size: 25px;
    color: var(--button-text);
    text-transform: uppercase;
  }
  .cta__chip {
    width: 32px; height: 32px;
    border-radius: 50%;
    background: var(--button-chip);
    display: flex; align-items: center; justify-content: center;
  }
  .caption {
    position: absolute;
    left: 0; top: 572px;
    width: 1200px;
    text-align: center;
    font-family: "Roboto Condensed", Arial, sans-serif;
    font-weight: 700;
    font-size: 54px;
    line-height: 60px;
    color: var(--caption-grey);
    text-transform: uppercase;
  }
</style>
</head>
<body>
  <section class="banner">
    <svg class="banner__bands" width="548" height="544" viewBox="0 0 548 544">
      <defs>
        <linearGradient id="band-green" x1="0" y1="0" x2="0" y2="1">
          <stop offset="0" stop-color="var(--green-light)"/>
          <stop offset="1" stop-color="var(--green-dark)"/>
        </linearGradient>
      </defs>
      <path d="M0 0 H548 V40 C400 70 200 40 0 82 Z" fill="url(#band-green)"/>
      <path d="M0 82 C200 40 400 70 548 40 V54 C400 80 200 56 0 96 Z" fill="var(--swoosh-yellow)"/>
      <path d="M0 470 C160 430 380 450 548 408 V544 H0 Z" fill="url(#band-green)"/>
      <path d="M0 456 C160 418 380 438 548 396 V408 C380 450 160 430 0 470 Z" fill="var(--swoosh-yellow)"/>
    </svg>

    <div class="banner__photo" role="img" aria-label="Photo of a smiling slim woman in sportswear measuring her waist and pointing forward"></div>
    <div class="banner__product" role="img" aria-label="Product visual: diet plan book cover and CD"></div>

    <h1 class="banner__title">Persönlicher Diätplan zum Abnehmen?</h1>

    <svg class="banner__cursor" width="30" height="46" viewBox="0 0 30 46" aria-hidden="true">
      <path d="M2 2 L2 36 L10 28 L16 42 L22 39 L16 26 L27 26 Z" fill="#ffffff" stroke="#333333" stroke-width="2" stroke-linejoin="round"/>
    </svg>

    <div class="brand"><span class="brand__name">Your<br>FitRoute</span></div>

    <a class="cta">
      <span class="cta__label">Jetzt informieren</span>
      <span class="cta__chip">
        <svg width="14" height="16" viewBox="0 0 14 16" aria-hidden="true"><path d="M4 2 L11 8 L4 14" fill="none" stroke="#ffffff" stroke-width="3"/></svg>
      </span>
    </a>
  </section>

  <p class="caption">Check the link in the description<br>to see the animation</p>
</body>
</html>
```